Brookvale Building Company - advertisement poster

I am looking to print some canvas signs to advertise my general contracting company, Brookvale Building Company. The sign will measure 6' long x 3' high so the size should match that ratio. I already have a logo icon, which is the Letter 'B' and some trees that I would like to incorporate, see attached. I would also like the to have the following information listed:
1) phone number: 831-555-0172
2) email: brookvalebuildingcompany@mailnest.example
3) website: brookvalebuildingcompany.example
4) Lic#4826130
5) I want to use this text: "BUILD WITH THE B-CREW!"

The ad should be relatively simple and clean. Black and Green are my company colors. I am open to creative ideas!

Target Market(s)

People looking to renovate their homes

Industry/Entity Type

Construction

Colors
59FF00
82FF00
B8FF75
E3FFCB
F4FFEA

Requirements
Must have
• Must have my company logo
Should not have
• No photos or complex graphics

```html
<!DOCTYPE html>
<html lang="en">
<head>
<meta charset="utf-8">
<title>Brookvale Building Company – Sign</title>
<link rel="stylesheet" href="https://fonts.googleapis.com/css2?family=Michroma&family=Montserrat:wght@700;800&family=Poppins:wght@600&display=swap">
<style>
  :root {
    --backdrop: #959595;
    --navy: #171c63;
    --green: #6ab533;
    --white: #ffffff;
    --charcoal: #262626;
    --ink: #1f1f1f;
  }
  * { margin: 0; padding: 0; box-sizing: border-box; }
  html, body { width: 1200px; height: 865px; overflow: hidden; }
  body { background: var(--backdrop); position: relative; }

  .sign {
    position: absolute; left: 87px; top: 176px;
    width: 1027px; height: 512px; overflow: hidden;
    background: var(--white);
  }
  .sign__top { position: absolute; left: 0; top: 0; width: 100%; height: 288px; background: var(--navy); }
  .sign__footer {
    position: absolute; left: 0; top: 430px; width: 100%; height: 82px;
    background: var(--charcoal); color: var(--white);
    font-family: "Poppins", sans-serif; font-weight: 600;
    font-size: 31px; letter-spacing: 6.4px; text-align: center; line-height: 82px;
  }

  .brand { position: absolute; left: 33px; top: 40px; width: 305px; text-align: center; }
  .brand__mark { width: 92px; height: 92px; margin: 0 auto 18px; background: var(--green); }
  .brand__name {
    font-family: "Michroma", sans-serif; color: var(--white);
    font-size: 28px; line-height: 1.15; letter-spacing: 1px;
  }
  .brand__name small { display: block; font-size: 14.5px; letter-spacing: 3.4px; margin-top: 6px; }

  .headline { position: absolute; left: 404px; top: 50px; width: 590px; }
  .headline__big {
    font-family: "Michroma", sans-serif; color: var(--green);
    font-size: 116px; line-height: 1; letter-spacing: -4px;
    transform: scaleY(1.22); transform-origin: top left; white-space: nowrap;
  }
  .headline__sub {
    margin-top: 30px;
    font-family: "Michroma", sans-serif; color: var(--white);
    font-size: 43px; letter-spacing: -1px; white-space: nowrap; font-weight: 700;
  }
  .headline__sub em { font-style: normal; color: var(--green); }

  .phone {
    position: absolute; left: 41px; top: 262px; width: 944px; height: 94px;
    background: var(--green); border: 3px solid var(--white); border-radius: 9px;
    display: flex; align-items: center;
  }
  .phone__icon { width: 62px; height: 62px; margin-left: 35px; flex: none; }
  .phone__number {
    margin-left: 27px;
    font-family: "Montserrat", sans-serif; font-weight: 800; color: var(--white);
    font-size: 86px; letter-spacing: 3px; line-height: 1;
  }

  .details {
    position: absolute; left: 40px; top: 372px; width: 960px; height: 44px;
    display: flex; align-items: center;
    font-family: "Poppins", sans-serif; font-weight: 600; color: var(--ink);
  }
  .details__license { font-size: 29px; }
  .details__license b { color: var(--navy); font-weight: 600; }
  .details__mail { margin-left: 34px; display: flex; align-items: center; font-size: 25px; }
  .details__mail svg { width: 34px; height: 24px; margin-right: 16px; }
</style>
</head>
<body>
  <main class="sign">
    <div class="sign__top"></div>

    <div class="brand">
      <div class="brand__mark"></div>
      <div class="brand__name">BROOKVALE<small>BUILDING COMPANY</small></div>
    </div>

    <div class="headline">
      <div class="headline__big">BUILD</div>
      <div class="headline__sub">WITH THE <em>B-CREW</em></div>
    </div>

    <div class="phone">
      <svg class="phone__icon" viewBox="0 0 62 62" aria-hidden="true">
        <circle cx="31" cy="31" r="31" fill="#fff"/>
        <path d="M21 15c2-1 4 0 5 2l3 6c1 2 0 3-1 4l-2 2c1 4 5 8 9 10l2-2c1-1 3-2 4-1l6 3c2 1 3 3 2 5l-2 3c-2 2-5 3-8 2-10-3-18-11-21-21-1-3 0-6 2-8z" fill="#6ab533"/>
        <path d="M34 18a11 11 0 0 1 10 10M34 12a17 17 0 0 1 16 16" fill="none" stroke="#6ab533" stroke-width="3" stroke-linecap="round"/>
      </svg>
      <span class="phone__number">831-555-0172</span>
    </div>

    <div class="details">
      <span class="details__license"><b>LIC</b> #4826130</span>
      <span class="details__mail">
        <svg viewBox="0 0 34 24" aria-hidden="true">
          <rect x="1.5" y="1.5" width="31" height="21" fill="none" stroke="#171c63" stroke-width="3"/>
          <path d="M2 2l15 12L32 2M2 22l11-10M32 22L21 12" fill="none" stroke="#171c63" stroke-width="3"/>
        </svg>
        brookvalebuildingcompany@mailnest.example
      </span>
    </div>

    <div class="sign__footer">brookvalebuildingcompany.example</div>
  </main>
</body>
</html>
```